Webpage for co-working space for tech startups

We have an established co-working space in Aalborg Denmark where we have around 30 companies sharing office space. We are starting a new chapter for us and would like to have a new graphical image - new logo and new webpage, but keep the same name. The webpage should be professional, but also "fun", not too serious. We are all about working hard on our companies, but also taking some time off in between and being social and having fun. We are not corporate, but want to project the image that we are serious about what we do.

We currently have a black/red logo (see www.hivedesk.dk or test.hivedesk.dk), but are interesting in having a new logo design, so colour can be chosen freely. Currently our logo is a big HIVE and a little desk underneath the HIVE. The new logo will be one word "hivedesk" with a small logo before or on top.

If we can make a good webpage for this project, then I have a second more simple project which is also a small single page wordpress site which I would also like to have made.

Target Market(s)

tech startups - relatively new companies, typically younger people 20-35 with a tech background - business or programming, preferably both

Industry/Entity Type

HIVE

Logo Text

hivedesk

Coding

Coded - Design and coding required

Number of Pages Required

4 page

Font styles to use
Sans Serif

Colors

Designer to choose colors to be used in the design.

Requirements
Must have
• Wordpress CMS.
• Mobile and PC optimized
• 2 languages - English and Danish
• Four sections, could be four pages, or four sections of a single page.
• "Home", "Residents", "Our Working Space", "Our Event Space"
• Footer of page or pages should have contact information.
• "Home" has some information about who we are and what we do
• "Residents" has a list of all our residents - it should be possible to easily add and removed new / old residents - See one example here: http://test.hivedesk.dk/en_GB/beboere/ or another example here: http://www.hivedesk.dk/beboere/ - one of our colleagues http://pilotbarn.dk/startups/ or another one of our colleagues http://www.brightkelpyard.dk/residents/
• "Our working space" will have a description of our building, a map of where it is and a bunch of photos which show the different offices, meeting rooms and people working
• "Our events space" will have a description of our event spaces, details of cost + different arrangments of furniture, and lots of photos of events, see here for an example http://www.hivedesk.dk/lej-vores-lokaler/
• Our current webpage - www.hivedesk.dk was put together very quickly and has not really been optimized. We started a new webpage test.hivedesk.dk, but it was never really finished.
• We are looking for a simple webpage, not too much going on. Examples of some of our colleagues in the business http://pilotbarn.dk/, http://www.brightkelpyard.dk/,
Nice to have
• http://www.brightkelpyard.dk/ is a really good template for us. If we can get something like this, we are happy.

```html
<!DOCTYPE html>
<html lang="en">
<head>
<meta charset="utf-8">
<title>hivedesk — Co-Working Space</title>
<link href="https://fonts.googleapis.com/css2?family=Montserrat:wght@400;600;700&family=Open+Sans:wght@400;600&display=swap" rel="stylesheet">
<style>
:root{
  --blue:#2ea3dc;
  --blue-dark:#1f86bb;
  --ink:#3b3b3b;
  --muted:#8a8a8a;
  --light:#f3f3f3;
  --rule:#e2e2e2;
  --footer:#262626;
  --footer-text:#bdbdbd;
  --white:#ffffff;
}
*{box-sizing:border-box;margin:0;padding:0}
html,body{width:1200px;height:4684px;overflow:hidden}
body{font-family:"Open Sans",Arial,sans-serif;color:var(--ink);background:var(--white);position:relative}
h1,h2,h3,h4{font-family:"Montserrat",Arial,sans-serif}
section,header,footer{position:absolute;left:0;width:1200px}

/* nav */
.site-nav{top:0;height:72px;z-index:2;display:flex;align-items:center;padding:0 190px}
.site-nav a{color:var(--white);text-decoration:none;font-size:13px;font-weight:600;padding:0 18px;height:72px;display:flex;align-items:center}
.site-nav a.active{background:var(--blue)}
.lang{margin-left:auto;display:flex;align-items:center;gap:6px;color:var(--white);font-size:12px}
.lang .select{width:78px;height:22px;background:var(--blue);display:flex;align-items:center;padding-left:8px}

/* hero */
.hero{top:0;height:660px;background:linear-gradient(180deg,#5d6468 0%,#8d9396 45%,#6b7174 100%)}
.hero-copy{position:absolute;left:190px;top:340px;color:var(--white)}
.hero-copy h1{font-size:44px;font-weight:700;line-height:1.1;letter-spacing:1px}
.hero-copy h1 .big{font-size:70px;display:block}
.hero-copy p{width:640px;margin-top:22px;font-size:14px;line-height:1.6}
.brand{position:absolute;left:540px;top:80px;display:flex;align-items:center;gap:10px;color:var(--white);font-family:"Montserrat",sans-serif;font-weight:700;font-size:26px}
.brand i{width:18px;height:18px;background:var(--blue);display:block}

/* headings */
.section-title{text-align:center;font-size:30px;font-weight:600;color:var(--ink)}
.section-title .box{border:3px solid var(--blue);padding:2px 8px;color:var(--blue)}
.section-title.light{color:var(--white)}
.section-title.light .box{border-color:var(--white);color:var(--white)}
.rule{width:800px;height:1px;background:var(--rule);margin:20px auto 0}
.btn{display:block;margin:0 auto;width:170px;height:40px;border:2px solid var(--blue);color:var(--blue);font-size:12px;font-weight:600;text-align:center;line-height:36px;letter-spacing:1px}
.btn.solid{background:var(--blue);color:var(--white)}

/* about */
.about{top:660px;height:420px;padding-top:84px;background:var(--white)}
.about p{width:820px;margin:26px auto 0;text-align:center;font-size:14px;line-height:1.7;color:var(--muted)}
.about .btn{margin-top:40px}

/* resident */
.resident{top:1080px;height:470px;padding-top:26px}
.resident-row{display:flex;gap:40px;margin:50px 0 0 192px}
.resident-photo{width:416px;height:280px;background:linear-gradient(135deg,#b45a3c,#d9c7a7 55%,#7f9a5b)}
.resident-text{width:440px;padding-top:4px}
.resident-text h3{color:var(--blue);font-size:26px;font-weight:600}
.resident-text p{font-size:13px;line-height:1.7;color:var(--muted);margin-top:14px}
.resident-text .btn{margin:28px 0 0}

/* working space */
.desks{top:1550px;height:210px;background:var(--white)}
.desks svg{display:block}
.working{top:1760px;height:470px;background:var(--blue);padding-top:70px}
.gallery{display:flex;gap:10px;justify-content:center;margin-top:44px}
.gallery div{width:262px;height:180px}
.g1{background:linear-gradient(135deg,#1d5b6b,#3fa07b)}
.g2{background:linear-gradient(180deg,#bcd3e3,#8a6e55 60%,#5f7c3a)}
.g3{background:linear-gradient(135deg,#2b2f33,#6a6f74)}
.arrows{display:flex;justify-content:center;gap:18px;margin-top:30px}

/* facilities */
.facilities{top:2230px;height:570px;padding-top:86px;background:var(--light)}
.fac-grid{display:grid;grid-template-columns:repeat(3,260px);gap:44px 60px;justify-content:center;margin-top:46px}
.fac h4{display:flex;align-items:center;gap:10px;font-size:11px;font-weight:600;letter-spacing:.5px;color:var(--ink)}
.fac p{font-size:12px;line-height:1.6;color:var(--muted);margin:10px 0 0 38px}
.facilities .btn{margin-top:48px}

/* showcase */
.showcase{top:2800px;height:560px;background:linear-gradient(180deg,#fdfdfd 0%,#eeeeee 58%,#c79a63 72%,#a9773f 100%)}
.showcase-screen{position:absolute;left:250px;top:36px;width:700px;height:400px;background:linear-gradient(135deg,#0e5ea8,#2a8fe0 55%,#0b3f7a)}
.showcase-base{position:absolute;left:230px;top:436px;width:740px;height:74px;background:linear-gradient(180deg,#c8c8c8,#8e8e8e)}
.showcase-copy{position:absolute;left:420px;top:110px;width:360px;color:var(--white);text-align:center}
.showcase-copy h2{font-size:28px;font-weight:600;line-height:1.25}
.showcase-copy h2 .box{border:3px solid var(--white);padding:0 6px}
.showcase-copy p{font-size:11px;margin-top:12px;line-height:1.5}
.showcase-copy .btn{border-color:var(--white);color:var(--white);margin-top:18px;width:140px;height:34px;line-height:30px}

/* events */
.events{top:3360px;height:820px;padding-top:126px}
.event-row{display:flex;gap:16px;justify-content:center;margin-top:50px}
.event{width:400px}
.event .photo{height:248px}
.e1{background:linear-gradient(135deg,#3b2f2a,#a37d64 55%,#e3d6c8)}
.e2{background:linear-gradient(135deg,#f2efe9,#c9b89c 60%,#7a6a54)}
.event .card{background:var(--light);height:200px;text-align:center;padding-top:22px}
.event h3{color:var(--blue);font-size:24px;font-weight:600}
.event .meta{font-size:12px;color:var(--ink);margin-top:6px;line-height:1.5}
.event .meta span{color:var(--blue);display:block}
.event p{font-size:12px;color:var(--muted);line-height:1.6;width:300px;margin:10px auto 0}
.note{width:824px;margin:20px auto 0;font-size:12px;color:var(--muted)}
.note b{color:var(--blue)}
.events .btn{margin-top:40px}

/* partners */
.partners{top:4180px;height:160px;background:var(--light);display:flex;justify-content:space-around;align-items:center;padding:0 150px}
.partner{font-family:"Montserrat",sans-serif;font-weight:600;font-size:16px;color:#455a6e;display:flex;align-items:center;gap:8px}
.partner i{width:14px;height:14px;background:#455a6e;display:block}

/* footer */
.site-footer{top:4340px;height:344px;background:var(--footer);color:var(--footer-text)}
.footer-brand{position:absolute;left:540px;top:28px;display:flex;align-items:center;gap:8px;color:var(--white);font-family:"Montserrat",sans-serif;font-weight:700;font-size:22px}
.footer-brand i{width:14px;height:14px;background:var(--blue);display:block}
.footer-cols{position:absolute;left:190px;top:110px;display:flex;gap:0}
.footer-col{width:200px}
.footer-col h4{color:var(--white);font-size:14px;font-weight:600;letter-spacing:1px}
.footer-col ul{list-style:none;margin-top:12px;font-size:12px;line-height:1.8;color:var(--blue)}
.subscribe{width:260px}
.subscribe .field{display:flex;margin-top:12px}
.subscribe .field span{flex:1;height:26px;background:var(--white);font-size:11px;color:var(--muted);padding:5px 8px}
.subscribe .field b{width:30px;height:26px;background:var(--blue)}
.subscribe small{display:block;font-size:10px;color:var(--blue);margin-top:10px}
.copyright{position:absolute;left:0;width:100%;top:300px;text-align:center;font-size:12px;border-top:1px solid #3a3a3a;padding-top:14px}
</style>
</head>
<body>

<section class="hero" role="img" aria-label="Photo of a bright office desk with monitors by large windows"></section>
<header class="site-nav">
  <a class="active">Home</a><a>Residents</a><a>Our Working Space</a><a>Our Event Space</a>
  <div class="lang"><span>EN</span><div class="select">English</div></div>
</header>
<div class="brand" style="position:absolute;z-index:2"><i></i>hivedesk</div>
<div class="hero-copy" style="position:absolute;z-index:2">
  <h1>HIVE<span class="big">CO-WORKING SPACE</span></h1>
  <p>Lorem ipsum is simply dummy text of the printing and typesetting industry. Lorem ipsum has been the standard dummy text ever since the 1500s.</p>
</div>

<section class="about">
  <h2 class="section-title"><span class="box">About</span> Hive</h2>
  <div class="rule"></div>
  <p>The co-working community at hivedesk is a community of tech entrepreneurs with great growth ambitions. Our vision is to create the best possible conditions for North Jutland entrepreneurs by offering them an environment where they can share knowledge, experience, contacts, ideas, motivation and a good time daily.</p>
  <p style="margin-top:14px">With its 2,500 m2, hivedesk can offer both individual offices, flex spaces, meeting rooms, a dedicated events area and smaller and larger workplaces. Contact us to arrange a visit about potential workplaces and available spaces.</p>
  <a class="btn">READ MORE</a>
</section>

<section class="resident">
  <h2 class="section-title"><span class="box">R</span>esident</h2>
  <div class="rule"></div>
  <div class="resident-row">
    <div class="resident-photo" role="img" aria-label="Photo of a red half-timbered building"></div>
    <div class="resident-text">
      <h3>Brovik in Hive Desk</h3>
      <p>At hivedesk we do not call the companies in the co-worker environment tenants; we much more than that. They are "residents". These smaller startups have come together to build something. They all have a spot in the community. There are no contracts, just a common attitude with people dedicated to building something with different, talented team-mates and growing potential customers.</p>
      <p>Learn more about what we offer residents.</p>
      <a class="btn">LEARN MORE</a>
    </div>
  </div>
</section>

<section class="desks" role="img" aria-label="Illustration of office chairs at desks with computer screens">
  <svg width="1200" height="210" viewBox="0 0 1200 210"><rect x="0" y="0" width="1200" height="210" fill="#ffffff"/><rect x="0" y="120" width="1200" height="90" fill="#2ea3dc" opacity=".95"/></svg>
</section>

<section class="working">
  <h2 class="section-title light"><span class="box">Our</span> Working Space</h2>
  <div class="gallery">
    <div class="g1" role="img" aria-label="Aerial map view of the building grounds"></div>
    <div class="g2" role="img" aria-label="Photo of the half-timbered building with trees"></div>
    <div class="g3" role="img" aria-label="Photo of an office interior"></div>
  </div>
  <div class="arrows">
    <svg width="26" height="14" viewBox="0 0 26 14"><path d="M26 7H3M9 1L3 7l6 6" stroke="#fff" stroke-width="2" fill="none"/></svg>
    <svg width="26" height="14" viewBox="0 0 26 14"><path d="M0 7h23M17 1l6 6-6 6" stroke="#fff" stroke-width="2" fill="none"/></svg>
  </div>
</section>

<section class="facilities">
  <h2 class="section-title"><span class="box">Work</span> Space Facilities</h2>
  <div class="rule"></div>
  <div class="fac-grid">
    <div class="fac"><h4><svg width="28" height="22" viewBox="0 0 28 22" fill="none" stroke="#2ea3dc" stroke-width="2"><path d="M2 8a17 17 0 0 1 24 0M6 12a11 11 0 0 1 16 0M10 16a5 5 0 0 1 8 0"/><circle cx="14" cy="20" r="1.5" fill="#2ea3dc"/></svg>UNLIMITED INTERNET</h4><p>Lorem ipsum is simply dummy text of the printing and typesetting industry.</p></div>
    <div class="fac"><h4><svg width="28" height="22" viewBox="0 0 28 22" fill="none" stroke="#2ea3dc" stroke-width="2"><path d="M4 6h16v8a6 6 0 0 1-6 6h-4a6 6 0 0 1-6-6zM20 8h3a3 3 0 0 1 0 6h-3"/></svg>FREE COFFE EVERYDAY</h4><p>Lorem ipsum is simply dummy text of the printing and typesetting industry.</p></div>
    <div class="fac"><h4><svg width="28" height="22" viewBox="0 0 28 22" fill="none" stroke="#2ea3dc" stroke-width="2"><rect x="2" y="5" width="24" height="13" rx="6"/><path d="M8 9v5M5.5 11.5h5"/><circle cx="19" cy="10" r="1" fill="#2ea3dc"/><circle cx="21" cy="13" r="1" fill="#2ea3dc"/></svg>GAME STATION</h4><p>Lorem ipsum is simply dummy text of the printing and typesetting industry.</p></div>
    <div class="fac"><h4><svg width="28" height="22" viewBox="0 0 28 22" fill="none" stroke="#2ea3dc" stroke-width="2"><path d="M3 3h14v9H9l-4 4v-4H3zM20 7h5v9h-2v3l-3-3h-6v-2"/></svg>MEETING ROOM</h4><p>Lorem ipsum is simply dummy text of the printing and typesetting industry.</p></div>
    <div class="fac"><h4><svg width="28" height="22" viewBox="0 0 28 22" fill="none" stroke="#2ea3dc" stroke-width="2"><rect x="3" y="2" width="22" height="13"/><path d="M14 15v5M9 20h10"/></svg>CONFERENCE ROOM</h4><p>Lorem ipsum is simply dummy text of the printing and typesetting industry.</p></div>
    <div class="fac"><h4><svg width="28" height="22" viewBox="0 0 28 22" fill="none" stroke="#2ea3dc" stroke-width="2"><rect x="3" y="2" width="22" height="18"/><path d="M10 2v18M18 2v18M7 9v3M14 9v3M22 9v3"/></svg>DEDICATED LOCKERS</h4><p>Lorem ipsum is simply dummy text of the printing and typesetting industry.</p></div>
  </div>
  <a class="btn">VIEW ALL FACILITIES</a>
</section>

<section class="showcase" role="img" aria-label="Photo of a laptop on a wooden table">
  <div class="showcase-screen"></div>
  <div class="showcase-base"></div>
  <div class="showcase-copy">
    <h2><span class="box">Our</span> Modern Office Spaces Are Simply Stunning</h2>
    <p>Lorem ipsum is simply dummy text of the printing and typesetting industry.</p>
    <a class="btn">BOOK A TOUR</a>
  </div>
</section>

<section class="events">
  <h2 class="section-title"><span class="box">Our</span> Event Space</h2>
  <div class="rule"></div>
  <div class="event-row">
    <div class="event">
      <div class="photo e1" role="img" aria-label="Photo of guests talking at a daytime event"></div>
      <div class="card">
        <h3>DAY EVENT</h3>
        <div class="meta">Lounge Area<span>Rent of the lounge, 8:00 - 16:00</span></div>
        <p>Morning meeting for 30 guests. We serve you breakfast, water, organic tea and coffee from our in-house kitchen to get you all going.</p>
      </div>
    </div>
    <div class="event">
      <div class="photo e2" role="img" aria-label="Photo of a table set with drinks for a reception"></div>
      <div class="card">
        <h3>STANDING RECEPTION</h3>
        <div class="meta">Canteen Area<span>Rent of the canteen, 16:00 - 22:00</span></div>
        <p>When you have something to celebrate. For 50 guests. Light finger food, wine and beer available. Refreshments are included.</p>
      </div>
    </div>
  </div>
  <p class="note"><b>NOTE -</b> If you need to rent the premises for a shorter period or in the evening hours, the hourly rate is 475,- ex VAT.</p>
  <a class="btn">VIEW MORE EVENTS</a>
</section>

<section class="partners">
  <div class="partner"><i></i>Harborline</div>
  <div class="partner">Tonehall</div>
  <div class="partner">Northvane</div>
  <div class="partner">Saltreed Media</div>
</section>

<footer class="site-footer">
  <div class="footer-brand"><i></i>hivedesk</div>
  <div class="footer-cols">
    <div class="footer-col"><h4>ABOUT</h4><ul><li>About Us</li><li>Contact Us</li><li>FAQ</li><li>Privacy</li></ul></div>
    <div class="footer-col"><h4>SPACE</h4><ul><li>Residents</li><li>Working Space</li><li>Event Space</li></ul></div>
    <div class="footer-col"><h4>LEGAL</h4><ul><li>Terms of Use</li><li>Privacy Policy</li><li>Cookies</li></ul></div>
    <div class="footer-col subscribe"><h4>SUBSCRIBE</h4><div class="field"><span>Email Address</span><b></b></div><small>Sign up for news from hivedesk</small></div>
  </div>
  <div class="copyright">© Copyright 2016 _hivedesk All Right Reserved</div>
</footer>

</body>
</html>
```